Business Card Design - Amberfield Court

We are looking at a new design for our business cards that has a modern and professional look. We run a residential aged care facility focussing on the care of residents. The cards will be used for potential clients, consultants and business opportunities in this sector. Blue and white is our main colours and would to see these colours incorporated in the design.
Industry/Entity Type
Business
Contact Information for Business Card
Amberfield Court, Darren Walsh, dwalsh@amberfieldcourt.com.au, Finance Manager, 0472 639 208, BCom, 37 Marrabel Crescent, Brindle Vale, Qld 4093.
Look and feel
Each slider illustrates characteristics of the customer's brand and the style your logo design should communicate.

```html
<!DOCTYPE html>
<html lang="en">
<head>
<meta charset="utf-8">
<title>Amberfield Court – Business Card</title>
<link rel="stylesheet" href="https://fonts.googleapis.com/css2?family=Open+Sans:wght@400;600&display=swap">
<style>
  :root {
    --backdrop: #3b3431;
    --card: #0f0f10;
    --brand-blue: #5b86a6;
    --text-white: #f2f2f2;
    --text-grey: #9a9a9a;
    --divider: #6a6a6a;
  }
  html, body {
    margin: 0;
    padding: 0;
    overflow: hidden;
  }
  body {
    width: 1200px;
    height: 814px;
    background: var(--backdrop);
    font-family: "Open Sans", Arial, sans-serif;
    display: flex;
    align-items: center;
    justify-content: center;
    gap: 50px;
  }
  .card {
    width: 525px;
    height: 300px;
    background: var(--card);
    position: relative;
    box-shadow: 0 10px 30px rgba(0,0,0,.45);
  }

  /* Front */
  .brand-lockup {
    position: absolute;
    top: 78px;
    left: 150px;
    width: 300px;
    display: flex;
    align-items: center;
    justify-content: center;
    gap: 10px;
  }
  .brand-mark {
    width: 20px;
    height: 20px;
    border-radius: 50%;
    background: var(--brand-blue);
  }
  .brand-name {
    color: var(--brand-blue);
    font-size: 21px;
    font-weight: 600;
    letter-spacing: .5px;
  }
  .person {
    position: absolute;
    left: 20px;
    top: 186px;
    width: 268px;
    text-align: right;
  }
  .person-name {
    color: var(--brand-blue);
    font-size: 19px;
    font-weight: 600;
    line-height: 24px;
    margin: 0;
  }
  .person-name .credential {
    font-size: 14px;
    font-weight: 400;
  }
  .person-role {
    color: var(--text-grey);
    font-size: 14px;
    line-height: 20px;
    margin: 2px 0 2px;
  }
  .person-email {
    color: var(--text-white);
    font-size: 14px;
    line-height: 20px;
    margin: 0;
  }
  .divider {
    position: absolute;
    left: 300px;
    top: 150px;
    width: 1px;
    height: 92px;
    background: var(--divider);
  }
  .contact {
    position: absolute;
    left: 312px;
    top: 148px;
    color: var(--text-white);
    font-size: 12.5px;
    line-height: 20px;
    margin: 0;
    padding: 0;
    list-style: none;
  }
  .contact li {
    display: flex;
    align-items: center;
    gap: 7px;
    white-space: nowrap;
  }
  .contact svg {
    width: 11px;
    height: 11px;
    fill: var(--brand-blue);
  }

  /* Back */
  .back-name {
    position: absolute;
    top: 108px;
    width: 100%;
    text-align: center;
    color: var(--text-white);
    font-size: 24px;
    font-weight: 600;
    letter-spacing: .5px;
    margin: 0;
  }
  .back-web {
    position: absolute;
    top: 156px;
    width: 100%;
    text-align: center;
    color: var(--text-white);
    font-size: 13px;
    letter-spacing: 2px;
    margin: 0;
  }
</style>
</head>
<body>
  <section class="card card-front">
    <div class="brand-lockup">
      <span class="brand-mark"></span>
      <span class="brand-name">Amberfield Court</span>
    </div>
    <div class="person">
      <p class="person-name">Darren Walsh <span class="credential">BCom</span></p>
      <p class="person-role">Finance Manager</p>
      <p class="person-email">dwalsh@amberfieldcourt.com.au</p>
    </div>
    <div class="divider"></div>
    <ul class="contact">
      <li>37 Marrabel Crescent</li>
      <li>Brindle Vale, Qld 4093.</li>
      <li>
        <svg viewBox="0 0 24 24" aria-hidden="true"><path d="M6.6 10.8a15.1 15.1 0 0 0 6.6 6.6l2.2-2.2a1 1 0 0 1 1-.25 11.4 11.4 0 0 0 3.6.57 1 1 0 0 1 1 1V20a1 1 0 0 1-1 1A17 17 0 0 1 3 4a1 1 0 0 1 1-1h3.5a1 1 0 0 1 1 1c0 1.25.2 2.45.57 3.57a1 1 0 0 1-.25 1z"/></svg>
        0472 639 208
      </li>
      <li>
        <svg viewBox="0 0 24 24" aria-hidden="true"><circle cx="12" cy="12" r="10"/></svg>
        www.amberfieldcourt.com.au
      </li>
    </ul>
  </section>

  <section class="card card-back">
    <p class="back-name">Amberfield Court</p>
    <p class="back-web">www.amberfieldcourt.com.au</p>
  </section>
</body>
</html>
```